Birchline Septic Solutions

Would like to see some single sided ones but would also like to see some double sided with one sided only being the logo. Owners name is Colin Vandro. Phone number is 555-214-0387
Services are pumping, inspections, installs, and repairs

Contact Information for Business Card

555-241-0387 Colin Vandro Maple Hollow, OH

```html
<!DOCTYPE html>
<html lang="en">
<head>
<meta charset="utf-8">
<title>Birchline Septic Solutions – Business Cards</title>
<link href="https://fonts.googleapis.com/css2?family=Open+Sans:wght@400;600;700;800&display=swap" rel="stylesheet">
<style>
  :root {
    --stage: #232323;
    --card: #1f1f22;
    --card-deep: #19191c;
    --card-deeper: #151518;
    --teal: #2bbcb4;
    --white: #ffffff;
    --soft: #ececec;
    --emboss: #2c2c30;
  }
  * { margin: 0; padding: 0; box-sizing: border-box; }
  html, body {
    width: 1200px; height: 779px; overflow: hidden;
    background: var(--stage);
    font-family: "Open Sans", sans-serif;
  }
  .canvas {
    position: relative; width: 1200px; height: 779px;
    display: flex; justify-content: center; align-items: center; gap: 80px;
  }
  .card {
    position: relative; width: 300px; height: 525px;
    background: var(--card); border-radius: 18px; overflow: hidden;
    box-shadow: 0 18px 40px rgba(0,0,0,.45);
  }
  /* Logo side */
  .card--logo { display: flex; align-items: center; justify-content: center; }
  .emboss-name {
    color: var(--emboss); font-weight: 800; font-size: 40px; line-height: 1.05;
    text-align: center; text-transform: uppercase; letter-spacing: 1px;
  }
  .emboss-name small { display: block; font-size: 17px; letter-spacing: 4px; margin-top: 8px; }
  /* Info side */
  .waves { position: absolute; inset: 0; }
  .brand {
    position: absolute; top: 58px; left: 0; right: 0;
    display: flex; flex-direction: column; align-items: center; gap: 10px;
    color: var(--white); font-weight: 800; text-transform: uppercase; text-align: center;
  }
  .brand-mark { width: 14px; height: 14px; background: var(--white); }
  .brand-name { font-size: 38px; line-height: 1; letter-spacing: 1px; }
  .brand-sub { font-size: 13px; letter-spacing: 4px; }
  .contact {
    position: absolute; top: 215px; left: 0; right: 0; text-align: center; color: var(--white);
  }
  .owner { font-size: 24px; font-weight: 700; line-height: 1.2; }
  .owner .first { color: var(--teal); font-weight: 600; }
  .town { font-size: 14px; font-weight: 400; color: var(--soft); margin-top: 2px; }
  .phone-icon { display: block; margin: 10px auto 4px; }
  .phone { font-size: 21px; font-weight: 400; letter-spacing: .5px; }
  .services { position: absolute; top: 400px; left: 0; right: 0; text-align: center; color: var(--white); }
  .services-pill {
    display: inline-block; background: var(--teal); color: var(--white);
    font-size: 13px; font-weight: 600; padding: 3px 22px; border-radius: 50%;
    text-transform: uppercase;
  }
  .services-arrow { display: block; margin: 2px auto 4px; }
  .services-list { list-style: none; font-size: 14px; font-weight: 400; line-height: 1.3; }
</style>
</head>
<body>
<main class="canvas">
  <section class="card card--logo" aria-label="Logo side">
    <p class="emboss-name">Birchline<small>Septic Solutions</small></p>
  </section>

  <section class="card card--info" aria-label="Contact side">
    <svg class="waves" viewBox="0 0 300 525" aria-hidden="true">
      <path d="M0 300 Q170 340 300 250 L300 525 L0 525 Z" fill="var(--card-deep)"/>
      <path d="M80 525 Q150 380 300 330 L300 525 Z" fill="var(--card-deeper)"/>
    </svg>
    <header class="brand">
      <span class="brand-mark"></span>
      <span class="brand-name">Birchline</span>
      <span class="brand-sub">Septic Solutions</span>
    </header>
    <div class="contact">
      <p class="owner"><span class="first">Colin</span> Vandro</p>
      <p class="town">Maple Hollow, OH</p>
      <svg class="phone-icon" width="24" height="32" viewBox="0 0 24 32" aria-hidden="true">
        <circle cx="12" cy="11" r="10" fill="var(--teal)"/>
        <path d="M8 7 q0 7 7 8 l1.5-2 -2-1.5 -1.2 1 q-2.5-1-3.3-3.3 l1-1.2 -1.5-2 Z" fill="var(--white)"/>
        <path d="M12 22 v6 M8.5 25 L12 30 L15.5 25" stroke="var(--teal)" stroke-width="2" fill="none"/>
      </svg>
      <p class="phone">555-241-0387</p>
    </div>
    <div class="services">
      <span class="services-pill">Services</span>
      <svg class="services-arrow" width="14" height="12" viewBox="0 0 14 12" aria-hidden="true">
        <path d="M7 0 v6 M2 5 L7 11 L12 5" stroke="var(--teal)" stroke-width="2" fill="none"/>
      </svg>
      <ul class="services-list">
        <li>Installs</li>
        <li>Pumping</li>
        <li>Inspections</li>
        <li>And Repairs</li>
      </ul>
    </div>
  </section>
</main>
</body>
</html>
```